Basic business card

use my newly created logo - and the phrases (Faster Yield Gains & Streamlined Wafer Process Validation) - and my new email domain / ID - use at conferences / tradeshows

Industry/Entity Type

semiconductor

Contact Information for Business Card

Daniel K Forde, Owner, communicate via Logo - Lower COT - Cost of Test, Accelerated NPI - New Product Introduction, phone +1 555 613 0946, Larkfield, Westmoor, USA, daniel.forde@qal-vub.com

Font styles to use
Sans Serif

Requirements
Nice to have
• re-use my logo created via Pixel Harbor last August (#7315926)

```html
<!DOCTYPE html>
<html lang="en">
<head>
<meta charset="utf-8">
<title>QAL-VUB Business Card</title>
<link href="https://fonts.googleapis.com/css2?family=Montserrat:wght@400;500;700&display=swap" rel="stylesheet">
<style>
  :root {
    --stage: #c4c4c4;
    --card: #4a5874;
    --white: #ffffff;
    --green: #7cbf2a;
    --sky: #3fb6e6;
    --blue: #1f7ec4;
    --orange: #f39a1e;
    --emboss: #8d9ab3;
  }
  * { box-sizing: border-box; margin: 0; padding: 0; }
  html, body { width: 1200px; height: 788px; overflow: hidden; }
  body {
    background: var(--stage);
    font-family: "Montserrat", sans-serif;
    position: relative;
  }
  .card {
    position: absolute;
    top: 239px;
    width: 540px;
    height: 310px;
    background: var(--card);
    border-radius: 22px;
    overflow: hidden;
    box-shadow: 0 14px 30px rgba(0,0,0,.25);
  }
  .card--front { left: 40px; }
  .card--back { left: 620px; }

  /* front */
  .accent-square {
    position: absolute; top: 0; right: 28px;
    width: 30px; height: 26px; background: var(--green);
  }
  .holder { position: absolute; top: 40px; right: 72px; text-align: right; }
  .holder__name { color: var(--green); font-weight: 700; font-size: 27px; letter-spacing: .3px; }
  .holder__role { color: var(--white); font-size: 15px; margin-top: 2px; }

  .brand {
    position: absolute; left: 46px; top: 122px;
    color: var(--white); font-weight: 500; font-size: 46px; letter-spacing: 1px;
  }

  .contacts { position: absolute; left: 46px; bottom: 42px; list-style: none; }
  .contacts li {
    display: flex; align-items: center; gap: 10px;
    color: var(--white); font-size: 17px; line-height: 28px;
  }
  .contacts svg { width: 16px; height: 16px; fill: var(--sky); flex: none; }

  .edge-band { position: absolute; left: 0; right: 0; bottom: 0; height: 8px; display: flex; }
  .edge-band span { flex: 1; }
  .edge-band .orange { background: var(--orange); }
  .edge-band .sky { background: var(--sky); }
  .edge-band .green { background: var(--green); }
  .edge-band .blue { background: var(--blue); }

  /* back */
  .brand--large {
    position: absolute; left: 0; right: 0; top: 92px; text-align: center;
    color: var(--emboss); font-weight: 500; font-size: 70px; letter-spacing: 2px;
  }
  .tagline {
    position: absolute; left: 0; right: 0; bottom: 58px; text-align: center;
    color: var(--white); font-weight: 500; font-size: 15px; letter-spacing: .4px;
  }
  .tagline .sky { color: var(--sky); }
  .tagline .green { color: var(--green); }
</style>
</head>
<body>
  <section class="card card--front">
    <div class="accent-square"></div>
    <div class="holder">
      <p class="holder__name">Daniel K Forde</p>
      <p class="holder__role">Owner</p>
    </div>
    <p class="brand">QAL-VUB</p>
    <ul class="contacts">
      <li><svg viewBox="0 0 16 16"><path d="M3 1l3 3-1.6 2a9 9 0 0 0 5.6 5.6L12 10l3 3-2 2C7 15 1 9 1 3z"/></svg>+1 555 613 0946</li>
      <li><svg viewBox="0 0 16 16"><path d="M1 3h14v10H1z M1 3l7 6 7-6" /></svg>daniel.forde@qal-vub.com</li>
      <li><svg viewBox="0 0 16 16"><path d="M8 0a5.5 5.5 0 0 0-5.5 5.5C2.5 10 8 16 8 16s5.5-6 5.5-10.5A5.5 5.5 0 0 0 8 0zm0 7.7a2.2 2.2 0 1 1 0-4.4 2.2 2.2 0 0 1 0 4.4z"/></svg>Larkfield, Westmoor, USA</li>
    </ul>
    <div class="edge-band"><span class="orange"></span><span class="sky"></span><span class="green"></span><span class="blue"></span></div>
  </section>

  <section class="card card--back">
    <p class="brand--large">QAL-VUB</p>
    <p class="tagline">Faster <span class="sky">Yield Gains</span> &amp; Streamlined <span class="green">Wafer Process Validation</span></p>
  </section>
</body>
</html>
```